Q Linkora

Ned a new business card, need two designs one to be for communications and one to be for security.
Communications will have what we do on it which include:-
PABX systems
Data Cabling
Phone services
Fibre
Security
"your communications specialist in the Pilbara"
The Severity one will have on it:-
CCTV
Alarm
Access control
Security consulting
Communications services
"Your security partner in the Pilbara"
Target Market(s)
industry
Industry/Entity Type
Communications
Contact Information for Business Card
Marcus Delbrook
0427350912
marcus@qlinkora.com.au
www.qlinkora.com.au

```html
<!DOCTYPE html>
<html lang="en">
<head>
<meta charset="utf-8">
<title>Q Linkora – Business Card</title>
<link rel="stylesheet" href="https://fonts.googleapis.com/css2?family=Raleway:wght@400;500&family=Open+Sans:ital,wght@0,400;0,600;0,700;1,400&display=swap">
<style>
  :root {
    --backdrop: #1c1c1d;
    --card: #2f3034;
    --card-edge: #26272a;
    --orange: #f4a334;
    --white: #f2f2f2;
    --soft: #d4d4d6;
    --grey: #7d7e82;
  }
  * { margin: 0; padding: 0; box-sizing: border-box; }
  html, body {
    width: 1200px; height: 900px; overflow: hidden;
    background: var(--backdrop);
  }
  .canvas { position: relative; width: 1200px; height: 900px; }

  .card {
    position: absolute;
    width: 543px; height: 316px;
    background: var(--card);
    border-radius: 16px;
    box-shadow: 0 6px 14px rgba(0,0,0,0.55);
  }
  .card--front { left: 331px; top: 121px; }
  .card--back  { left: 332px; top: 488px; }

  /* Front */
  .brand-mark {
    position: absolute; left: 92px; top: 132px;
    display: flex; align-items: center; gap: 8px;
  }
  .brand-mark .dot {
    width: 16px; height: 16px; border-radius: 50%;
    background: var(--orange);
  }
  .brand-mark .name {
    font-family: "Raleway", sans-serif; font-weight: 500;
    font-size: 26px; color: var(--grey);
  }
  .holder {
    position: absolute; left: 282px; top: 106px;
    font-family: "Raleway", sans-serif;
  }
  .holder-name { font-size: 26px; font-weight: 400; color: var(--white); line-height: 30px; }
  .holder-name .surname { color: var(--orange); }
  .holder-role { font-size: 16px; color: var(--soft); line-height: 20px; margin-left: 1px; }
  .contacts {
    position: absolute; left: 286px; top: 175px;
    font-family: "Raleway", sans-serif; font-size: 14px;
    color: var(--soft); line-height: 18px; list-style: none;
  }

  /* Back */
  .back-brand {
    position: absolute; left: 0; right: 0; top: 82px;
    display: flex; justify-content: center; align-items: center; gap: 8px;
  }
  .back-brand .dot {
    width: 14px; height: 14px; border-radius: 50%;
    background: var(--grey);
  }
  .back-brand .name {
    font-family: "Open Sans", sans-serif; font-weight: 700;
    font-size: 34px; color: var(--orange); letter-spacing: 0.5px;
  }
  .services {
    position: absolute; left: 0; right: 0; top: 174px;
    text-align: center; font-family: "Open Sans", sans-serif;
    font-size: 15px; color: var(--white); line-height: 26px;
    word-spacing: 1px;
  }
  .services .sep { margin: 0 8px; }
  .tagline {
    position: absolute; left: 0; right: 0; top: 244px;
    text-align: center; font-family: "Open Sans", sans-serif;
    font-style: italic; font-size: 15px; color: var(--white);
  }
</style>
</head>
<body>
<main class="canvas">
  <section class="card card--front">
    <div class="brand-mark">
      <span class="dot"></span>
      <span class="name">qlinkora</span>
    </div>
    <div class="holder">
      <p class="holder-name">Marcus <span class="surname">Delbrook</span></p>
      <p class="holder-role">Managing Director</p>
    </div>
    <ul class="contacts">
      <li>marcus@qlinkora.com.au</li>
      <li>www.qlinkora.com.au</li>
      <li>0427350912</li>
    </ul>
  </section>

  <section class="card card--back">
    <div class="back-brand">
      <span class="dot"></span>
      <span class="name">qlinkora</span>
    </div>
    <div class="services">
      <p>PABX systems<span class="sep">|</span>Data Cabling<span class="sep">|</span>Phone services</p>
      <p>Fibre<span class="sep">|</span>Security</p>
    </div>
    <p class="tagline">"your communications specialist in the Pilbara"</p>
  </section>
</main>
</body>
</html>
```